Clear Plastic Card Design

I am looking to have a business card designed from my logo icon. I am looking to match the style of a different business card I have attached in the files.
Looking for a card that is plastic, with layers of transparency in the shape of my logo icon (also attached in the files) - not a circle like the other card. The winning design will incorporate the red icon logo on the front and back and include the charity's name, "Light for the Weary Souls" in the same or similar font, as well as an email and phone number. For now, use the email: email@lightfortheweary-mail.org and the phone number 555-382-7194.
We like how the sample business card has transparency, partial and full opacity layers and a matching color scheme. Files will need to be in vector so that our business card printing company can work with it.
UPDATE:
We've some excellent designs in, thank you everyone! I got an early review from the owner, and he requested a minor redirect to find his perfect design. He wants the design to stand out by NOT being a rectangle. Try instead a circle, square, or best yet - something that falls in the outline of the logo icon, either fully or partially. Thank you, everyone!
Light for the Weary Souls text should be incorporated as well as a phone and email.

```html
<!DOCTYPE html>
<html lang="en">
<head>
<meta charset="utf-8">
<title>Light for the Weary Souls – Round Business Card</title>
<link href="https://fonts.googleapis.com/css2?family=Oswald:wght@500;600&family=Montserrat:wght@400&display=swap" rel="stylesheet">
<style>
  :root {
    --bg: #b4b4b4;
    --card-light: #ffffff;
    --card-dark: #383838;
    --brand-red: #d0142c;
    --brand-orange: #e8501c;
    --ink: #111111;
    --paper: #ffffff;
  }
  * { box-sizing: border-box; margin: 0; padding: 0; }
  html, body { width: 1200px; height: 800px; overflow: hidden; }
  body {
    background: var(--bg);
    position: relative;
    font-family: "Oswald", "Arial Narrow", sans-serif;
  }
  .card {
    position: absolute;
    top: 160px;
    width: 480px;
    height: 480px;
    border-radius: 50%;
  }
  .card--front { left: 90px; background: var(--card-light); }
  .card--back { left: 630px; background: var(--card-dark); }

  .brand {
    position: absolute;
    display: flex;
    align-items: center;
    gap: 12px;
    font-family: "Montserrat", sans-serif;
    font-weight: 400;
    line-height: 1.15;
  }
  .brand__mark { background: var(--brand-red); flex: none; }
  .card--front .brand { left: 118px; top: 70px; font-size: 22px; color: var(--brand-red); }
  .card--front .brand__mark { width: 40px; height: 40px; }
  .card--back .brand { left: 88px; top: 196px; font-size: 34px; color: var(--paper); }
  .card--back .brand__mark { width: 56px; height: 56px; }

  .contact {
    position: absolute;
    left: 48px;
    display: flex;
    align-items: center;
    gap: 14px;
    color: var(--ink);
  }
  .contact__icon {
    width: 40px; height: 40px;
    border-radius: 10px;
    background: var(--brand-orange);
    display: flex; align-items: center; justify-content: center;
  }
  .contact--phone { top: 204px; font-size: 31px; font-weight: 500; }
  .contact--email { top: 258px; font-size: 18px; font-weight: 500; letter-spacing: 0.2px; }
  .contact__domain { color: var(--brand-red); }

  .arc-title {
    position: absolute; inset: 0;
    width: 480px; height: 480px;
  }
  .arc-title text {
    font-family: "Oswald", sans-serif;
    font-weight: 600;
    font-size: 30px;
    letter-spacing: 1.5px;
    fill: var(--brand-red);
  }
</style>
</head>
<body>
  <section class="card card--front" aria-label="Card front">
    <div class="brand">
      <span class="brand__mark"></span>
      <span class="brand__name">Light for the<br>Weary Souls</span>
    </div>

    <div class="contact contact--phone">
      <span class="contact__icon">
        <svg width="22" height="22" viewBox="0 0 24 24" aria-hidden="true">
          <path d="M6.6 10.8a15 15 0 0 0 6.6 6.6l2.2-2.2a1 1 0 0 1 1-.25 11.4 11.4 0 0 0 3.6.57 1 1 0 0 1 1 1V20a1 1 0 0 1-1 1A17 17 0 0 1 3 4a1 1 0 0 1 1-1h3.5a1 1 0 0 1 1 1c0 1.25.2 2.45.57 3.57a1 1 0 0 1-.25 1z" fill="#fff"/>
        </svg>
      </span>
      <span class="contact__text">555-382-7194</span>
    </div>

    <div class="contact contact--email">
      <span class="contact__icon">
        <svg width="20" height="20" viewBox="0 0 24 24" aria-hidden="true">
          <path d="M2 11 22 3l-6 18-4-7-10-3zm10 3 4-6-6 4" fill="#fff"/>
        </svg>
      </span>
      <span class="contact__text">EMAIL<span class="contact__domain">@LIGHTFORTHEWEARY-MAIL</span>.ORG</span>
    </div>

    <svg class="arc-title" viewBox="0 0 480 480" aria-hidden="false">
      <defs>
        <path id="bottom-arc" d="M 30 250 A 210 210 0 0 0 450 250"/>
      </defs>
      <text>
        <textPath href="#bottom-arc" startOffset="50%" text-anchor="middle">• LIGHT FOR THE WEARY SOULS •</textPath>
      </text>
    </svg>
  </section>

  <section class="card card--back" aria-label="Card back">
    <div class="brand">
      <span class="brand__mark"></span>
      <span class="brand__name">Light for the<br>Weary Souls</span>
    </div>
  </section>
</body>
</html>
```